Hi Designers,

I will need 4 web pages designed. The web page looks like an App (if you click on the logo, or the icon on an iPad, it will take you to the website), but it is still a webpage.

Please check the attachment on this brief to understand what specific pages I need to be designed.

A .PSD (straight-up PhotoShop image) as final deliverable is fine, as long as you give us the exact “web color numbers”.

The design is for desktop and iPad but in a single unified web application, NOT separate web app and (native) iPad app.

Details:

Brightwater Policy Partners is developing a browser-based application for use on any mobile device or desktop. The app will be used by corporations to communicate with their employees regarding legal, regulatory and company requirements for conducting business. The app is known as “Harbor Guidance Portal.” When the user clicks on the icon for Harbor Guidance Portal, they will enter a site full of information that a company deems necessary for the employee to do his/her job. There are several content sections within the site, including a login page, training, policies, forms, news feeds and blogs.

The application has been built using Microsoft .NET, and fully supports CSS-type skinning; it uses traditional page layouts. We are seeking a product logo concept (image), a master application/desktop icon (image), as well as a full color scheme/theme/skin design for all areas of the application (header area, body text, menu bar, etc.) in the form of a CSS. The look should be clean, crisp and professional; nothing cartoony or whimsical. It should be easy to read and “airy”.

We have sketched prototypes for the basic application page layout that we can send as a next step of the process.
Updates

Screen shots have been uploaded to this project.  Please use them to guide your design.

Dear designers,

I apologize for the delay in providing feedback. My partners and I will provide feedback in a few days. Thank you for your patience.

Industry/Entity Type

Business

Font styles to use
Other font styles liked:
• see font on screen shots when uploaded

```html
<!DOCTYPE html>
<html lang="en">
<head>
<meta charset="utf-8">
<title>Harbor Guidance Portal – Sign In</title>
<link href="https://fonts.googleapis.com/css2?family=Source+Sans+3:wght@400;600&display=swap" rel="stylesheet">
<style>
  :root {
    --navy-deep: #0a2546;
    --navy: #0f2f57;
    --navy-light: #163b66;
    --brand-box: #0d3460;
    --card-top: #ffffff;
    --card-bottom: #bdbdbd;
    --card-border: #ffffff;
    --field-border: #b9b9b9;
    --field-text: #555555;
    --label-text: #3a3a3a;
    --orange-top: #ffab1a;
    --orange-bottom: #ff8400;
    --orange-edge: #d36c00;
    --accent-blue: #1e93dc;
    --white: #ffffff;
    --footer-band: rgba(120, 150, 190, 0.16);
  }
  * { box-sizing: border-box; margin: 0; padding: 0; }
  html, body { width: 1200px; height: 864px; overflow: hidden; }
  body {
    position: relative;
    font-family: "Source Sans 3", "Myriad Pro", Arial, sans-serif;
    color: var(--white);
  }
  .page-backdrop {
    position: absolute; inset: 0;
    background: radial-gradient(ellipse at 50% 40%, var(--navy-light) 0%, var(--navy) 45%, var(--navy-deep) 100%);
  }
  .client-badge {
    position: absolute; left: 483px; top: 129px; width: 209px; height: 77px;
    background: var(--brand-box); border-radius: 3px;
    display: flex; align-items: center; padding: 12px 0 0 28px; gap: 16px;
  }
  .client-badge .dot { width: 40px; height: 40px; border-radius: 50%; background: var(--accent-blue); margin-top: -12px; }
  .client-badge .name { font-size: 15px; font-weight: 400; color: var(--white); }

  .login-card {
    position: absolute; left: 371px; top: 240px; width: 446px; height: 248px;
    border: 3px solid var(--card-border); border-radius: 7px;
    background: linear-gradient(to bottom, var(--card-top) 0%, #f0f0f0 30%, var(--card-bottom) 100%);
    box-shadow: 0 2px 10px rgba(0,0,0,0.4);
  }
  .field {
    position: absolute; left: 53px; width: 337px; height: 30px;
    border: 1px solid var(--field-border); border-radius: 8px;
    background: linear-gradient(to bottom, #ececec 0%, #ffffff 40%);
    box-shadow: inset 0 1px 2px rgba(0,0,0,0.12);
    display: flex; align-items: center; padding-left: 12px; gap: 10px;
    font-size: 12px; color: var(--field-text);
  }
  .field-user { top: 48px; }
  .field-pass { top: 99px; }
  .field svg { width: 14px; height: 14px; flex: none; }
  .options {
    position: absolute; left: 61px; top: 147px;
    display: flex; align-items: center; font-size: 12px; color: var(--label-text);
  }
  .options .check {
    width: 13px; height: 13px; border: 1px solid #2a6aa8; background: #fff; margin-right: 12px;
  }
  .options .sep { margin: 0 8px; }
  .sign-in {
    position: absolute; left: 62px; top: 186px; width: 188px; height: 35px;
    border: 1px solid var(--orange-edge); border-radius: 5px;
    background: linear-gradient(to bottom, var(--orange-top), var(--orange-bottom));
    display: flex; align-items: center; padding-left: 28px; gap: 12px;
    font-family: inherit; font-size: 17px; color: var(--white);
  }
  .sign-in svg { width: 22px; height: 26px; }

  .portal-mark {
    position: absolute; left: 374px; top: 525px; height: 84px;
    display: flex; align-items: center; gap: 14px;
  }
  .portal-mark .dot { width: 76px; height: 76px; border-radius: 50%; background: var(--accent-blue); }
  .portal-mark .name { font-size: 23px; font-weight: 400; font-variant: small-caps; color: var(--white); letter-spacing: 0.3px; margin-top: 4px; }

  .site-footer {
    position: absolute; left: 0; top: 710px; width: 1200px; height: 122px;
    background: var(--footer-band);
    display: flex; align-items: center; justify-content: center;
    font-size: 12px; color: var(--white);
  }
  .site-footer p { margin: -8px 0 0 38px; }
</style>
</head>
<body>
  <div class="page-backdrop" role="img" aria-label="Dark navy damask patterned background"></div>

  <div class="client-badge">
    <span class="dot"></span>
    <span class="name">Quellora Labs</span>
  </div>

  <form class="login-card">
    <label class="field field-user">
      <svg viewBox="0 0 14 14"><circle cx="7" cy="4.5" r="3" fill="#7a8ea8"/><path d="M1.5 13c0-3.2 2.5-5 5.5-5s5.5 1.8 5.5 5z" fill="#3f78b5"/></svg>
      <span>User Name</span>
    </label>
    <label class="field field-pass">
      <svg viewBox="0 0 14 14"><path d="M2 12l1-3 7-7 2 2-7 7z" fill="#e3a21a"/><path d="M2 12l1-3 2 2z" fill="#555"/></svg>
      <span>Password</span>
    </label>
    <div class="options">
      <span class="check"></span>
      <span>Keep me signed in</span><span class="sep">|</span><span>Forgot Password?</span>
    </div>
    <button type="button" class="sign-in">
      <svg viewBox="0 0 22 26"><path d="M5 11V7a6 6 0 0 1 12 0v4" fill="none" stroke="#9a9a9a" stroke-width="2.5"/><rect x="2" y="11" width="18" height="14" rx="2" fill="#d9b24a"/><circle cx="11" cy="17" r="2" fill="#6b5314"/></svg>
      <span>Sign In</span>
    </button>
  </form>

  <div class="portal-mark">
    <span class="dot"></span>
    <span class="name">Harbor Guidance Portal</span>
  </div>

  <footer class="site-footer">
    <p>© 2013 Harbor Guidance Portal. All Rights Reserved</p>
  </footer>
</body>
</html>
```